Lucky Harbour Fun Casino Entertainment

Looking to update my business card and make it look more modern, stand out and eye catching.
We are are fun casino business in Australia (primarily Sydney). Blackjack and Roulette are our most popular games although we have pretty much every game available for hire that you would find in a real casino. The final design would need to be sleek and appeal to the more upmarket corporate sector.
We mainly cater for Corporate Events, Private Parties, Fundraising Events, Team Building, Poker Tournaments
I think I'd prefer the colour Black.

Target Market(s)

High-end Corporate

Industry/Entity Type

Events

Contact Information for Business Card

Rob Kendall
Director
1300 482 617
0433 728 591
info@luckyharbour.com.au
www.luckyharbour.com.au
Facebook & Instagram @luckyharbourevents (proper social icons preferred)

Colors
000000
0255a3

Requirements
Must have
• Front side:
• Logo
• Contact details
• 'Australia's #1 Fun Casino Specialists'
• Back:
• Logo
Nice to have
• Back:
• Corporate Events
• Private Parties
• Poker Tournaments
• Fundraising
• Props & Theming
• Photo Booth
• Horse Racing Events
• The Vegas Sign attached, maybe on the back of the card in the background...?

```html
<!DOCTYPE html>
<html lang="en">
<head>
<meta charset="utf-8">
<title>Lucky Harbour Productions – Business Card</title>
<link href="https://fonts.googleapis.com/css2?family=Montserrat:wght@400;600;700&display=swap" rel="stylesheet">
<style>
  :root {
    --stage: #2a2622;
    --card-black: #050505;
    --card-edge: #1a1a1a;
    --gold: #f2c01e;
    --gold-deep: #d99a0b;
    --white: #ffffff;
    --muted: #e9e9e9;
    --chip-ring: #1c1c1c;
    --chip-face: #2e2e2e;
  }
  * { box-sizing: border-box; margin: 0; padding: 0; }
  html, body { width: 1200px; height: 780px; overflow: hidden; }
  body {
    background: var(--stage);
    font-family: "Montserrat", sans-serif;
    display: flex;
    align-items: center;
    justify-content: center;
    gap: 90px;
  }
  .card {
    position: relative;
    width: 360px;
    height: 630px;
    background: var(--card-black);
    border-radius: 22px;
    overflow: hidden;
    box-shadow: 0 18px 40px rgba(0,0,0,.55);
    color: var(--white);
    text-align: center;
  }
  .web-band {
    position: absolute;
    left: 0; right: 0; bottom: 0;
    height: 78px;
    background: linear-gradient(180deg, var(--gold) 0%, var(--gold-deep) 100%);
    border-top: 3px solid var(--white);
    display: flex;
    align-items: center;
    justify-content: center;
    color: #111;
    font-size: 17px;
    font-weight: 600;
    letter-spacing: .5px;
  }

  /* Front */
  .front .brand {
    margin-top: 64px;
    display: flex;
    flex-direction: column;
    align-items: center;
    gap: 14px;
  }
  .brand-disc {
    width: 110px; height: 110px;
    border-radius: 50%;
    background: var(--chip-face);
    border: 10px solid var(--gold);
  }
  .brand-name {
    color: var(--gold);
    font-weight: 700;
    font-size: 24px;
    letter-spacing: 1px;
    text-transform: uppercase;
  }
  .person { margin-top: 34px; }
  .person-name {
    color: var(--gold);
    font-weight: 700;
    font-size: 23px;
    text-transform: uppercase;
    letter-spacing: 1px;
  }
  .person-role { font-size: 15px; margin-top: 2px; }
  .rule {
    width: 270px; height: 2px;
    background: var(--gold);
    margin: 14px auto;
  }
  .contacts { list-style: none; display: flex; flex-direction: column; gap: 7px; font-size: 16px; }
  .contacts li { display: flex; align-items: center; justify-content: center; gap: 8px; }
  .icon { width: 18px; height: 18px; flex: none; }
  .socials { display: flex; flex-direction: column; align-items: center; gap: 6px; font-size: 15px; }
  .social-dots { display: flex; gap: 8px; }
  .social-dots span { width: 20px; height: 20px; border-radius: 50%; background: var(--gold); }
  .tagline {
    margin-top: 18px;
    color: var(--gold);
    font-size: 18px;
    font-weight: 600;
    line-height: 1.35;
  }

  /* Back */
  .back .hero {
    position: absolute;
    top: 40px; left: 50%;
    transform: translateX(-50%);
    width: 330px; height: 330px;
    border-radius: 50%;
    background: radial-gradient(circle at 50% 40%, #3a3a3a 0%, var(--chip-ring) 70%);
    display: flex;
    flex-direction: column;
    align-items: center;
    justify-content: center;
  }
  .hero-name {
    color: var(--gold);
    font-weight: 700;
    font-size: 34px;
    line-height: 1.15;
    text-transform: uppercase;
    letter-spacing: 1px;
  }
  .services {
    position: absolute;
    top: 395px; left: 0; right: 0;
    list-style: none;
    font-size: 18px;
    font-weight: 600;
    line-height: 1.45;
    color: var(--muted);
  }
</style>
</head>
<body>

  <section class="card front" aria-label="Business card front">
    <div class="brand">
      <div class="brand-disc"></div>
      <div class="brand-name">Lucky Harbour</div>
    </div>

    <div class="person">
      <div class="person-name">Rob Kendall</div>
      <div class="person-role">Director</div>
    </div>
    <div class="rule"></div>

    <ul class="contacts">
      <li>
        <svg class="icon" viewBox="0 0 20 20"><circle cx="10" cy="10" r="10" fill="#f2c01e"/><path d="M7 5.5l1.6 2.4-1 1.1a7 7 0 0 0 3.4 3.4l1.1-1 2.4 1.6-.9 1.7c-3.9-.3-7.6-4-7.9-7.9z" fill="#050505"/></svg>
        1300 482 617
      </li>
      <li>
        <svg class="icon" viewBox="0 0 20 20"><circle cx="10" cy="10" r="10" fill="#f2c01e"/><rect x="7" y="4.5" width="6" height="11" rx="1" fill="#050505"/><rect x="8" y="6" width="4" height="7" fill="#f2c01e"/></svg>
        0433 728 591
      </li>
      <li>info@luckyharbour.com.au</li>
    </ul>
    <div class="rule"></div>

    <div class="socials">
      <div class="social-dots"><span></span><span></span></div>
      @luckyharbourevents
    </div>

    <p class="tagline">Australia's #1<br>Fun Casino Specialists</p>

    <div class="web-band">www.luckyharbour.com.au</div>
  </section>

  <section class="card back" aria-label="Business card back">
    <div class="hero" role="img" aria-label="Large casino chip emblem with company name">
      <div class="hero-name">Lucky Harbour<br>Productions</div>
    </div>

    <ul class="services">
      <li>Corporate Events</li>
      <li>Private Parties</li>
      <li>Poker Tournaments</li>
      <li>Fundraising</li>
      <li>Props &amp; Theming</li>
      <li>Photo Booth</li>
      <li>Horse Racing Events</li>
    </ul>

    <div class="web-band">www.luckyharbour.com.au</div>
  </section>

</body>
</html>
```